Web Design job - Condo Debts Collection Business needs a Web Design

I need a site for a client, who works with condo debts collection, and ensure all revenues provided by condo fees will be always available to the building manager of condo on a specific date, regardless of defaults.
I have the visual identity (logo, slogan and colors) of the company, and some requirements on layout (kind of slider, menu options, phone number on a noble position, etc) - maybe I can do a sketch, but I like the idea of give some freedom to designer.

*** PLEASE, we have no interest in templates. We want something new***

Target Market(s)

I have two targets for this design: - Condominium's building manager. This target is looking for a solution to overdue debts on it's condo. - Residents on condominiums. This target wants to live in a better place, where their neighbors pay their condominium fees on time.

Number of Pages Required

1 page

Requirements
Must have
• - Slider with title, some short text related, a nice image (I prefer happy and/or peaceful family, people doing business, happy friends, and so on).
• - I have a special attention to menu. I'm looking for one I can have a nice effect, more elegant, charming, kind of innovative.
• - Phone number on the top (or clearly visible).
• - Member log in area or icon on the top (or clearly visible).
• - News/articles area.
• - Modern fonts, with good quality, sans-serif on areas where reading is more intensive (prefer Google web-fonts).
• - Colors specified on attached files.
Nice to have
• - Clear background color, cause it's better to read larger texts (like articles). Dark backgrounds makes reading difficult.
• - A site with effects (like shadows, lines, curves, gradients, lights) is usually pretty.
• - I pay attention on beautiful footers.
Should not have
• - Images with a lot of money (I don't sell richness, I sell tranquility, peace, harmony, safety).
• - Poor menu.

```html
<!DOCTYPE html>
<html lang="en">
<head>
<meta charset="utf-8">
<title>Valora Cobrança Condominial</title>
<link href="https://fonts.googleapis.com/css2?family=Josefin+Sans:wght@400;600;700&family=Open+Sans:wght@400;600;700&display=swap" rel="stylesheet">
<style>
:root{
  --gold:#e9a21c;
  --gold-dark:#c98612;
  --gold-deep:#a8700f;
  --gold-pale:#f7e9c8;
  --cream:#fbf6ec;
  --ink:#2b2b2b;
  --text:#777;
  --line:#e6e0d4;
  --footer:#1d1d1d;
  --footer-text:#a9a9a9;
  --white:#fff;
}
*{margin:0;padding:0;box-sizing:border-box}
html,body{width:1200px;height:3356px;overflow:hidden;background:var(--white)}
body{position:relative;font-family:"Open Sans",sans-serif;color:var(--text);font-size:14px;line-height:1.7}
.abs{position:absolute}
h1,h2,h3,h4{font-family:"Josefin Sans",sans-serif;color:var(--ink)}
.btn{display:inline-block;font-family:"Open Sans",sans-serif;font-size:13px;font-weight:600;padding:8px 22px;border-radius:4px;background:var(--gold-dark);color:var(--white);border:2px solid var(--gold-dark)}
.btn-outline{background:var(--white);color:var(--gold-dark)}

/* header */
.site-header{left:0;top:0;width:1200px;height:108px;background:var(--white)}
.brand{left:100px;top:18px;display:flex;align-items:center;gap:12px}
.brand-square{width:38px;height:38px;background:var(--gold)}
.brand-name{font-family:"Josefin Sans",sans-serif;font-weight:700;font-size:40px;color:var(--ink);line-height:1}
.brand-tag{left:150px;top:60px;font-size:10px;letter-spacing:1px;color:var(--ink)}
.topbar{left:690px;top:12px;display:flex;gap:60px;font-size:13px;color:var(--ink);align-items:center}
.topbar span{display:flex;align-items:center;gap:8px}
.main-nav{left:390px;top:64px;width:740px;height:40px;background:var(--gold);display:flex}
.main-nav a{flex:1;text-align:center;line-height:40px;font-size:11px;font-weight:600;color:var(--white);border-right:1px solid rgba(255,255,255,.35);text-decoration:none}
.main-nav a.active{background:#f5c35a}

/* hero */
.hero{left:0;top:108px;width:1200px;height:512px;background:linear-gradient(135deg,#3f352a 0%,#7c6b55 35%,#b8a68c 60%,#5a4a3a 100%)}
.hero-shade{left:0;top:108px;width:1200px;height:512px;background:rgba(0,0,0,.25)}
.hero-title{left:0;top:240px;width:1200px;text-align:center;color:var(--white);font-family:"Josefin Sans",sans-serif;font-weight:700;font-size:84px;line-height:1}
.hero-sub{left:0;top:330px;width:1200px;text-align:center;color:var(--white);font-family:"Open Sans",sans-serif;font-size:36px;line-height:1.2}
.hero-dots{left:540px;top:564px;display:flex;gap:10px}
.hero-dots i{width:12px;height:12px;border-radius:50%;background:rgba(255,255,255,.6)}
.hero-dots i.on{background:var(--white)}
.hero-arrow{top:355px;width:32px;height:44px;background:rgba(0,0,0,.35)}

/* features */
.features-band{left:0;top:620px;width:1200px;height:120px;background:var(--gold)}
.features-bg{left:0;top:740px;width:1200px;height:300px;background:var(--cream)}
.feature{top:640px;width:260px}
.feature-head{display:flex;align-items:center;gap:14px;height:80px}
.feature-num{font-family:"Josefin Sans",sans-serif;font-weight:700;font-size:46px;color:var(--white)}
.feature-title{font-size:15px;font-weight:600;color:var(--white);line-height:1.3;text-transform:uppercase}
.feature p{margin-top:44px;font-size:12.5px;line-height:1.65}
.feature .btn{margin-top:22px}

/* about */
.section-title{left:0;width:1200px;text-align:center;font-size:44px;font-weight:600;line-height:1.2}
.title-rule{left:570px;width:60px;height:2px;background:var(--gold)}
.about-text{left:240px;top:1185px;width:720px;text-align:center;font-size:12.5px;line-height:1.75}
.about-actions{left:0;top:1290px;width:1200px;display:flex;justify-content:center;gap:20px}

/* what we do */
.wwd-photo{left:100px;top:1440px;width:600px;height:332px;background:linear-gradient(120deg,#4e4337,#8a7761 50%,#c9b59a)}
.wwd-title{left:770px;top:1450px;font-size:48px;font-weight:600}
.wwd-text{left:770px;top:1530px;width:330px;font-size:12.5px;line-height:1.75}
.wwd-btn{left:840px;top:1710px}

.divider{left:100px;width:1000px;height:1px;background:var(--line)}

/* services */
.service{width:330px}
.service h4{font-size:19px;font-weight:600}
.service p{margin-top:10px;font-size:12.5px;line-height:1.7}
.service p b{color:var(--gold-dark);font-weight:600}
.services-art{left:450px;top:1950px;width:300px;height:400px;background:linear-gradient(160deg,#f0c86a,#e9a21c 45%,#c98612 80%,#a8700f)}

/* articles */
.article{top:2490px;width:300px}
.article-photo{width:300px;height:205px}
.article-ribbon{display:block;margin:-16px auto 0;width:120px;height:22px;background:var(--gold);color:var(--white);font-size:10px;font-weight:600;text-align:center;line-height:22px;position:relative}
.article h3{margin-top:16px;font-family:"Open Sans",sans-serif;font-size:15px;font-weight:700;color:var(--ink)}
.article-meta{margin-top:6px;display:flex;gap:24px;font-size:10px;color:#999}
.article-meta span{display:flex;align-items:center;gap:6px}
.article p{margin-top:12px;font-size:12px;line-height:1.7}
.article .more{margin-top:10px;font-size:12px;font-weight:600;color:var(--gold-dark)}

/* footer */
.site-footer{left:0;top:3005px;width:1200px;height:351px;background:var(--footer);color:var(--footer-text)}
.social{left:100px;top:3060px;display:flex;gap:22px}
.social i{width:22px;height:22px;border-radius:50%;background:#3a3a3a}
.footer-mark{left:564px;top:3040px;width:72px;height:72px;border-radius:50%;background:var(--gold);border:4px solid #2e2e2e}
.footer-rule{top:3076px;height:1px;background:#3b3b3b}
.footer-name{left:0;top:3120px;width:1200px;text-align:center;font-family:"Josefin Sans",sans-serif;font-weight:700;font-size:20px;color:var(--white)}
.search{left:790px;top:3058px;width:300px;height:38px;display:flex}
.search span{flex:1;background:var(--white);font-size:12px;color:#999;line-height:38px;padding-left:12px}
.search b{width:44px;background:var(--gold)}
.footer-address{left:0;top:3160px;width:1200px;text-align:center;font-size:12px;line-height:1.7}
.footer-contact{top:3220px;width:260px;text-align:center;font-size:12px}
.footer-contact svg{display:block;margin:0 auto 6px}
.footer-bottom{left:0;top:3310px;width:1200px;text-align:center;font-size:10px;border-top:1px solid #333;padding-top:14px}
</style>
</head>
<body>

<header class="abs site-header">
  <div class="abs brand"><span class="brand-square"></span><span class="brand-name">valora</span></div>
  <div class="abs brand-tag">COBRANÇA CONDOMINIAL</div>
  <div class="abs topbar">
    <span><svg width="16" height="16" viewBox="0 0 16 16"><circle cx="8" cy="8" r="8" fill="#e9a21c"/><circle cx="8" cy="6" r="2.6" fill="#fff"/><path d="M3.5 13c1-2.6 8-2.6 9 0" fill="#fff"/></svg>Member Login</span>
    <span><svg width="16" height="16" viewBox="0 0 16 16"><circle cx="8" cy="8" r="8" fill="#e9a21c"/><path d="M5 4l2 0 1 2.5-1.2 1a6 6 0 0 0 2.7 2.7l1-1.2 2.5 1v2c-4.5.5-8.6-3.6-8-8z" fill="#fff"/></svg>Toll Free &nbsp;(81) 3000-0000</span>
  </div>
  <nav class="abs main-nav">
    <a class="active">HOME</a><a>ABOUT US</a><a>SERVICES</a><a>NEWS AND ARTICLES</a><a>OFFICE</a><a>PLACEMENT FORM</a>
  </nav>
</header>

<div class="abs hero" role="img" aria-label="Photo of business people reviewing documents at a meeting table"></div>
<div class="abs hero-shade"></div>
<div class="abs hero-arrow" style="left:0"></div>
<div class="abs hero-arrow" style="right:0"></div>
<h1 class="abs hero-title">VALORA</h1>
<div class="abs hero-sub">Cobrança Condominial</div>
<div class="abs hero-dots"><i class="on"></i><i></i><i></i><i></i></div>

<div class="abs features-band"></div>
<div class="abs features-bg"></div>
<svg class="abs" style="left:0;top:740px" width="1200" height="300" aria-hidden="true">
  <polygon points="0,300 0,120 160,300" fill="#f3e4c2" opacity=".6"/>
  <polygon points="1200,0 1200,260 1010,0" fill="#f3e4c2" opacity=".6"/>
</svg>
<div class="abs feature" style="left:100px">
  <div class="feature-head"><span class="feature-num">01</span><span class="feature-title">Commercial<br>Debt Recovery</span></div>
  <p>Lorem ipsum dolor sit amet, consectetur adipiscing elit, sed do eiusmod tempor incididunt ut labore et dolore magna aliqua. Ut enim ad minim veniam.</p>
  <span class="btn">Read More</span>
</div>
<div class="abs feature" style="left:460px">
  <div class="feature-head"><span class="feature-num">02</span><span class="feature-title">Legal Debt<br>Recovery</span></div>
  <p>Lorem ipsum dolor sit amet, consectetur adipiscing elit, sed do eiusmod tempor incididunt ut labore et dolore magna aliqua. Ut enim ad minim veniam.</p>
  <span class="btn">Read More</span>
</div>
<div class="abs feature" style="left:820px">
  <div class="feature-head"><span class="feature-num">03</span><span class="feature-title">On-Line Stat/<br>Placement</span></div>
  <p>Lorem ipsum dolor sit amet, consectetur adipiscing elit, sed do eiusmod tempor incididunt ut labore et dolore magna aliqua. Ut enim ad minim veniam.</p>
  <span class="btn">Read More</span>
</div>

<h2 class="abs section-title" style="top:1100px">About Us</h2>
<div class="abs title-rule" style="top:1166px"></div>
<p class="abs about-text">Lorem ipsum dolor sit amet, consectetur adipiscing elit, sed do eiusmod tempor incididunt ut labore et dolore magna aliqua. Ut enim ad minim veniam, quis nostrud exercitation ullamco laboris nisi ut aliquip ex ea commodo consequat. Duis aute irure dolor in reprehenderit in voluptate velit esse cillum dolore eu fugiat nulla pariatur.</p>
<div class="abs about-actions"><span class="btn">Read More</span><span class="btn btn-outline">Contact Now</span></div>
<div class="abs divider" style="top:1400px"></div>

<div class="abs wwd-photo" role="img" aria-label="Photo of a team of professionals talking around an office table"></div>
<h2 class="abs wwd-title">What We Do</h2>
<p class="abs wwd-text">Lorem ipsum dolor sit amet, consectetur adipiscing elit, sed do eiusmod tempor incididunt ut labore et dolore magna aliqua. Ut enim ad minim veniam, quis nostrud exercitation ullamco laboris nisi ut aliquip ex ea commodo consequat.</p>
<span class="abs btn wwd-btn">Read More</span>
<div class="abs divider" style="top:1880px"></div>

<div class="abs service" style="left:100px;top:1960px">
  <h4>Request For A Free Quote</h4>
  <p>Sed ut perspiciatis unde omnis iste natus error sit voluptatem accusantium doloremque laudantium, totam rem aperiam, eaque ipsa. <b>Read More »</b></p>
</div>
<div class="abs service" style="left:100px;top:2185px">
  <h4>Client Registration</h4>
  <p>Sed ut perspiciatis unde omnis iste natus error sit voluptatem accusantium doloremque laudantium, totam rem aperiam, eaque ipsa. <b>Read More »</b></p>
</div>
<div class="abs service" style="left:785px;top:1960px">
  <h4>Why Choose Us</h4>
  <p>Sed ut perspiciatis unde omnis iste natus error sit voluptatem accusantium doloremque laudantium, totam rem aperiam, eaque ipsa. <b>Read More »</b></p>
</div>
<div class="abs service" style="left:785px;top:2185px">
  <h4>How It Works</h4>
  <p>Sed ut perspiciatis unde omnis iste natus error sit voluptatem accusantium doloremque laudantium, totam rem aperiam, eaque ipsa. <b>Read More »</b></p>
</div>
<div class="abs services-art" role="img" aria-label="Decorative mosaic of gold triangles linking the four service topics"></div>

<h2 class="abs section-title" style="top:2400px">Articles</h2>
<div class="abs title-rule" style="top:2464px"></div>

<article class="abs article" style="left:100px">
  <div class="article-photo" role="img" aria-label="Photo of a happy family relaxing together in a park" style="background:linear-gradient(135deg,#8ea86a,#c9b58a 60%,#6f8a4e)"></div>
  <span class="article-ribbon">READ ARTICLE</span>
  <h3>SED UT PERSPICIATIS UNDE</h3>
  <div class="article-meta"><span>● 24/05/2016</span><span>● 16</span></div>
  <p>Duis aute irure dolor in reprehenderit in voluptate velit esse cillum dolore eu fugiat nulla pariatur. Excepteur sint occaecat cupidatat.</p>
  <div class="more">Read More »</div>
</article>
<article class="abs article" style="left:450px">
  <div class="article-photo" role="img" aria-label="Photo of a smiling couple embracing outdoors" style="background:linear-gradient(135deg,#6f8a9a,#c4b09a 55%,#8a7058)"></div>
  <span class="article-ribbon">READ ARTICLE</span>
  <h3>SED UT PERSPICIATIS UNDE</h3>
  <div class="article-meta"><span>● 24/05/2016</span><span>● 16</span></div>
  <p>Duis aute irure dolor in reprehenderit in voluptate velit esse cillum dolore eu fugiat nulla pariatur. Excepteur sint occaecat cupidatat.</p>
  <div class="more">Read More »</div>
</article>
<article class="abs article" style="left:800px">
  <div class="article-photo" role="img" aria-label="Photo of a peaceful couple sitting by the sea" style="background:linear-gradient(135deg,#a7bccb,#d8c7b0 55%,#8a9aa8)"></div>
  <span class="article-ribbon">READ ARTICLE</span>
  <h3>SED UT PERSPICIATIS UNDE</h3>
  <div class="article-meta"><span>● 24/05/2016</span><span>● 16</span></div>
  <p>Duis aute irure dolor in reprehenderit in voluptate velit esse cillum dolore eu fugiat nulla pariatur. Excepteur sint occaecat cupidatat.</p>
  <div class="more">Read More »</div>
</article>

<footer class="abs site-footer"></footer>
<div class="abs social"><i></i><i></i><i></i><i></i></div>
<div class="abs footer-rule" style="left:300px;width:250px"></div>
<div class="abs footer-rule" style="left:650px;width:120px"></div>
<div class="abs footer-mark"></div>
<div class="abs footer-name">valora</div>
<div class="abs search"><span>Search</span><b></b></div>
<div class="abs footer-address">Av. das Palmeiras, 450<br>Sala 210, Ed. Horizonte</div>
<div class="abs footer-contact" style="left:100px">
  <svg width="22" height="16" viewBox="0 0 22 16"><rect x="1" y="1" width="20" height="14" fill="none" stroke="#a9a9a9" stroke-width="1.5"/><path d="M1 1l10 8 10-8" fill="none" stroke="#a9a9a9" stroke-width="1.5"/></svg>
  contact@valora.example
</div>
<div class="abs footer-contact" style="left:840px">
  <svg width="18" height="18" viewBox="0 0 16 16"><path d="M3 1l3 0 1.5 3.5-1.8 1.3a8 8 0 0 0 3.5 3.5l1.3-1.8 3.5 1.5v3C7.5 15 1 8.5 3 1z" fill="#a9a9a9"/></svg>
  (81) 3000-0000
</div>
<div class="abs footer-bottom">© 2016 Copyrights Valora Cobrança Condominial All Rights Reserved</div>

</body>
</html>
```